Wine Bottle Label for Tall Fern Wines

We are a small, newly established winery in need of an original, bold and outstanding bottle label design for our Tall Fern wine.

Our vineyard and winery are located on a 200 acre farm in a remote part of southern Oregon. The name "Tall Fern" was inspired by the large, overgrown size of all of the foliage here, including our grapevines. Things grow large and vigorous in Oregon! And everything is very lush and green. It is almost surreal or other-worldly, like the landscapes seen in the Keeper of The Stones movies, or the land of Quill. It is a place that makes you say "wow" with its epic, large scale, natural beauty.

The name "Tall Fern" also captures the essence of our wine. It is big in flavor, quality and color. Our first release is a Pinot Noir (red). Pinot Noir wines often are subtle in flavor and thin in their color. Our label should convey that our Pinot Noir is a much more robust, darker, heavier, meatier, more flavorful wine that is a lot more fun than an "ordinary" wine. At the same time, this wine is not cheap, and so nothing in the label should convey "bargain," "low price," or "cheapness." This is a fine wine with a sense of adventure. Be sure to convey "quality" with your design along with "big," "adventure" and "fun".

The label should appeal to a younger demographic, both male and female, between the ages of 21 and 35. It should be non-traditional and adventurous and suggest a pushing of boundaries and a breaking of rules. This Pinot Noir does not conform to the normal "limitations" of the variety, therefore the label should not conform. It should have an "organic" or "natural" or "agricultural" vibe, as opposed to something mechanical or technical. It should, however, be contemporary. Do not confuse "natural" or "organic" with being nostalgic or old school. Think "agri-hipsters."

The label should be designed to fit on a Burgundy-style wine bottle (photo attached for reference). (Note: All Pinot Noir and Chardonnay is bottled in Burgundy bottles, If you are not sure about the bottle shape you can go to a local store and compare the various bottles. Locate a bottle of Pinot Noir or Chardonnay or anything identified as a "Burgundy Wine," and it should be the correct bottle. The tall, skinny bottles used for Cabernet Sauvignon are NOT correct)). Please see the "Must Have" notes for more on the bottle.

In summary, the final project should be a wine bottle label design that conveys bigness, vastness, adventurous, non-traditional, high quality wine. A good tagline to keep in mind is "Living Large."

Target Market(s)

Young, hip, non-conformist wine drinkers aged 21-35 with a sense of adventure and an appreciation of quality.

Industry/Entity Type

School

Requirements
Must have
• *Must contain the words:

Tall Fern (the brand)
2013 Pinot Noir (the vintage year and variety)

*The label must be designed to fit a Burgundy-style wine bottle. A photo is attached for reference.

*Additionally, the label needs to fit on the lower, widest part of the bottle. The label will be printed on sticky paper and rolled onto the bottle with a machine. The machine cannot apply labels to the neck of the bottle. The maximum size of a label that will fit this space is 5.5 inches wide by 4.5 inches tall. You DO NOT have to fill ALL of this space or confine the label shape to a rectangle, but the label cannot exceed this size or it won't stick to the bottle properly. It will really help if you can put your hands on an actual bottle to see the logistics of applying the label. But if that is not possible, just do your best with the instructions you have. I am confident the winning design could be adjusted to fit the bottle, if necessary
Nice to have
• *Wine grape leaf or leaves.

*A concept I have been playing with is sunlight shining through leaves like light through a Marlowe lamp or a stained glass window. This is NOT a requirement for this label. However, if the concept inspires and idea, I would be most happy to see it.
Should not have
• IF a leaf or leaves are included in the design (not a requirement) they MUST be wine grapevine leafs and preferably leaves of the Pinot Noir vine. Do not use generic leaves or identifiable leaves such as oak leaves, maple leaves, or anything that looks like the Canadian flag or the Halden Ridge Ravens hockey logo. Reference the attached photos of wine grape leaves to see the correct leaf type. I am happy to email more photos upon request. These photos may be used in whole or in part in your design, however, a leaf from a photo is NOT a requirement, nor is the image of a leaf or leaves.

This label should NOT be designed for Bordeaux-style wine bottles (the tall, skinny ones).

```html
<!DOCTYPE html>
<html lang="en">
<head>
<meta charset="utf-8">
<title>Tall Fern 2013 Pinot Noir Label</title>
<link rel="stylesheet" href="https://fonts.googleapis.com/css2?family=Lato:ital,wght@0,300;1,300&display=swap">
<style>
  :root {
    --ink-black: #050304;
    --wine-deep: #1e0d15;
    --wine-mid: #5a2940;
    --wine-light: #7d3c58;
    --leaf-dark: #2f6a12;
    --leaf-mid: #5fae22;
    --leaf-bright: #9bd640;
    --leaf-halo: rgba(235, 240, 200, 0.55);
    --type-light: #e9efe0;
    --type-glow: rgba(220, 235, 160, 0.6);
  }
  * { margin: 0; padding: 0; box-sizing: border-box; }
  html, body {
    width: 1200px;
    height: 592px;
    overflow: hidden;
    background: var(--ink-black);
  }
  .label {
    position: relative;
    width: 1200px;
    height: 592px;
    overflow: hidden;
    font-family: "Lato", "Helvetica Neue", Arial, sans-serif;
    background:
      linear-gradient(110deg,
        transparent 0%,
        transparent 52%,
        rgba(5, 3, 4, 0.55) 60%,
        transparent 68%,
        transparent 100%),
      linear-gradient(100deg,
        var(--ink-black) 0%,
        var(--wine-deep) 30%,
        var(--wine-mid) 48%,
        var(--wine-light) 62%,
        var(--wine-mid) 78%,
        var(--wine-light) 100%);
  }
  .label__vignette {
    position: absolute;
    inset: 0;
    background: radial-gradient(ellipse 60% 80% at 0% 100%, rgba(0,0,0,0.85), transparent 70%);
  }
  .leaf-halo {
    position: absolute;
    left: -40px;
    top: -50px;
    width: 480px;
    height: 440px;
    background: radial-gradient(ellipse at 48% 45%, var(--leaf-halo) 0%, rgba(200,210,160,0.25) 40%, transparent 70%);
  }
  .leaf-photo {
    position: absolute;
    left: 6px;
    top: 4px;
    width: 396px;
    height: 344px;
    border-radius: 46% 52% 40% 48% / 44% 46% 54% 50%;
    background: radial-gradient(ellipse at 45% 35%, var(--leaf-bright) 0%, var(--leaf-mid) 45%, var(--leaf-dark) 100%);
  }
  .brand-name {
    position: absolute;
    left: 600px;
    top: 170px;
    font-size: 150px;
    font-weight: 300;
    letter-spacing: -2px;
    line-height: 1;
    color: var(--type-light);
  }
  .vintage {
    position: absolute;
    left: 56px;
    top: 488px;
    font-size: 58px;
    font-weight: 300;
    line-height: 1;
    color: var(--type-light);
    text-shadow: 0 0 6px var(--type-glow);
  }
  .vintage__variety { font-style: italic; }
</style>
</head>
<body>
  <main class="label">
    <div class="label__vignette"></div>
    <div class="leaf-halo"></div>
    <div class="leaf-photo" role="img" aria-label="Photograph of a bright green Pinot Noir grapevine leaf, backlit"></div>
    <h1 class="brand-name">TallFern</h1>
    <p class="vintage">2013 <span class="vintage__variety">Pinot Noir</span></p>
  </main>
</body>
</html>
```